Modern Business Card

Modern professional business card with more than just logo and demographic info. Something memorable.

We are a trendy/modern chiropractic group with an emphasis on neurology, hence the minimalist-type brain logo. We want to convey that modern and technical aspect with professionalism and the elite nature of our practice environment.

```html
<!DOCTYPE html>
<html lang="en">
<head>
<meta charset="utf-8">
<title>Meridian Spine – Business Card</title>
<link rel="stylesheet" href="https://fonts.googleapis.com/css2?family=Alegreya:wght@700&family=Arimo:wght@400&family=Marcellus&display=swap">
<style>
  :root {
    --backdrop: #d9d9d9;
    --card: #1e1e1d;
    --card-edge: #2a2a29;
    --white: #f4f4f4;
    --grey-text: #c8c8c8;
    --rule: #3a3a39;
    --accent: #4a8ad3;
    --silver: #bdbdbd;
    --decor-top: rgba(255,255,255,0.07);
    --decor-bottom: rgba(255,255,255,0);
  }
  * { margin: 0; padding: 0; box-sizing: border-box; }
  html, body { width: 1200px; height: 900px; overflow: hidden; }
  body {
    background: var(--backdrop);
    position: relative;
    font-family: "Arimo", Arial, sans-serif;
  }
  .card {
    position: absolute;
    left: 333px;
    width: 553px;
    height: 343px;
    border-radius: 14px;
    background: var(--card);
    border: 1px solid var(--card-edge);
    box-shadow: 0 4px 10px rgba(0,0,0,0.25);
    overflow: hidden;
  }
  .card--front { top: 92px; }
  .card--back { top: 471px; }

  .decor {
    position: absolute;
    top: 0;
    border-radius: 0 0 40px 40px;
    background: linear-gradient(180deg, var(--decor-top), var(--decor-bottom));
  }
  .card--front .decor { left: 10px; width: 336px; height: 266px; }
  .card--back .decor { left: 10px; width: 346px; height: 262px; }

  .brand {
    position: absolute;
    display: flex;
    align-items: center;
    gap: 14px;
    font-family: "Marcellus", Georgia, serif;
    white-space: nowrap;
    letter-spacing: 1px;
  }
  .brand__mark { width: 26px; height: 26px; background: var(--accent); }
  .brand__name { font-size: 40px; line-height: 1; color: var(--white); }
  .card--front .brand { right: 32px; top: 90px; }
  .card--back .brand { left: 0; right: 0; top: 152px; justify-content: center; }
  .card--back .brand__mark { background: var(--silver); }
  .card--back .brand__name { color: var(--silver); }

  .person { position: absolute; left: 30px; top: 194px; }
  .person__name {
    font-family: "Alegreya", Georgia, serif;
    font-weight: 700;
    font-size: 17px;
    letter-spacing: 0.5px;
    color: var(--accent);
    line-height: 20px;
  }
  .person__title { font-size: 15px; color: var(--grey-text); line-height: 20px; }
  .divider {
    position: absolute;
    left: 207px; right: 32px; top: 205px;
    height: 1px; background: var(--rule);
  }

  .contacts { position: absolute; left: 30px; top: 248px; list-style: none; }
  .contacts li {
    display: flex; align-items: center; gap: 8px;
    font-size: 16px; color: var(--grey-text); line-height: 20.5px;
  }
  .contacts svg { width: 18px; height: 18px; flex: none; }
  .contacts .highlight { color: var(--accent); }

  .address {
    position: absolute; right: 32px; top: 269px;
    text-align: right; font-size: 16px; line-height: 20.5px;
    color: var(--grey-text); font-style: normal;
  }
</style>
</head>
<body>
  <section class="card card--front" aria-label="Card front">
    <div class="decor" role="img" aria-label="Faint background decoration of tall rounded bars"></div>
    <div class="brand">
      <span class="brand__mark"></span>
      <span class="brand__name">MERIDIAN SPINE</span>
    </div>

    <div class="person">
      <p class="person__name">DANIEL REYES</p>
      <p class="person__title">Managing Director</p>
    </div>
    <div class="divider"></div>

    <ul class="contacts">
      <li>
        <svg viewBox="0 0 18 18" aria-hidden="true">
          <rect x="1" y="1" width="16" height="16" rx="2" fill="none" stroke="var(--accent)" stroke-width="1.5"/>
          <path d="M6 4.5l2 2-1 1.3c.6 1.3 1.6 2.3 2.9 2.9l1.3-1 2 2-1.2 1.5c-3.6-.4-6.8-3.6-7.2-7.2z" fill="var(--accent)"/>
        </svg>
        044-987 210 345
      </li>
      <li>
        <svg viewBox="0 0 18 18" aria-hidden="true">
          <rect x="1" y="3.5" width="16" height="11" fill="var(--accent)"/>
          <path d="M1 3.5l8 6 8-6" fill="none" stroke="var(--card)" stroke-width="1.3"/>
        </svg>
        hello@meridianspine.com
      </li>
      <li>
        <svg viewBox="0 0 18 18" aria-hidden="true" fill="none" stroke="var(--accent)" stroke-width="1.4">
          <circle cx="9" cy="9" r="7.5"/>
          <ellipse cx="9" cy="9" rx="3.3" ry="7.5"/>
          <path d="M1.5 9h15M3 5h12M3 13h12"/>
        </svg>
        <span>www.<span class="highlight">meridianspine</span>.com</span>
      </li>
    </ul>

    <address class="address">
      421, Address line here<br>
      Country Name, 45452
    </address>
  </section>

  <section class="card card--back" aria-label="Card back">
    <div class="decor" role="img" aria-label="Faint background decoration of tall rounded bars"></div>
    <div class="brand">
      <span class="brand__mark"></span>
      <span class="brand__name">MERIDIAN SPINE</span>
    </div>
  </section>
</body>
</html>
```